Book cover design for my new Bankruptcy Law Book

Hi

I would like to get a unique and nice design for my new book titled: "Creditor Remedies Within Gulf Trade Statutes".

I like blue color. It will be in Arabic so I care the most about the design of the book cover and not the words on the cover as the printing company will handle the rest.

Much appreciated,

YUSUF BIN TAREQ

Colors
0692cd
33a6d7
86cae7
85abd2
3277b5
0255a3

Requirements
Must have
• Blue color
Nice to have
• pictures or shapes related to bankruptcy or insolvency

```html
<!DOCTYPE html>
<html lang="en">
<head>
<meta charset="utf-8">
<title>Creditor Remedies Within Gulf Trade Statutes — Cover Designs</title>
<link href="https://fonts.googleapis.com/css2?family=Amiri:wght@400;700&display=swap" rel="stylesheet">
<style>
  :root {
    --stage: #ffffff;
    --navy-deep: #060f3a;
    --navy-mid: #0c2160;
    --navy-top: #12306f;
    --gold-light: #e3cf9c;
    --gold: #b8975a;
    --gold-dark: #8c6e3a;
    --paper: #f3f3f3;
    --paper-edge: #e4e4e4;
    --ink: #1c1c1c;
    --royal: #2f4f99;
    --royal-deep: #26418a;
    --rule-grey: #8d8d8d;
    --crash-red: #e3231c;
  }
  * { margin: 0; padding: 0; box-sizing: border-box; }
  html, body {
    width: 1200px; height: 1000px; overflow: hidden;
    background: var(--stage);
    font-family: "Amiri", "Times New Roman", serif;
  }
  .canvas { position: relative; width: 1200px; height: 1000px; }

  .cover { position: absolute; overflow: hidden; box-shadow: 0 10px 28px rgba(0,0,0,.22); }

  /* Navy edition */
  .cover--navy {
    left: 140px; top: 150px; width: 420px; height: 700px;
    background: linear-gradient(180deg, var(--navy-top) 0%, var(--navy-mid) 35%, var(--navy-deep) 100%);
  }
  .cover--navy .pattern-field {
    position: absolute; left: 0; top: 0; width: 100%; height: 120px;
    background: linear-gradient(180deg, rgba(60,95,170,.35), rgba(60,95,170,0));
  }
  .cover--navy .title-block { position: absolute; right: 20px; top: 165px; width: 330px; text-align: center; color: #fff; }
  .cover--navy .chart-art {
    position: absolute; left: 0; top: 300px; width: 250px; height: 260px;
    background: linear-gradient(135deg, rgba(227,207,156,.55), rgba(140,110,58,.35) 60%, rgba(140,110,58,0));
  }
  .cover--navy .band-rule {
    position: absolute; left: 0; bottom: 112px; width: 100%; height: 12px;
    background: var(--navy-deep);
    border-top: 3px solid var(--gold); border-bottom: 3px solid var(--gold);
  }
  .cover--navy .author-band {
    position: absolute; left: 0; bottom: 0; width: 100%; height: 112px;
    background: linear-gradient(90deg, var(--gold-dark), var(--gold-light) 45%, var(--gold) 100%);
    display: flex; align-items: center; justify-content: center;
  }
  .cover--navy .author { color: var(--navy-deep); }

  /* White edition */
  .cover--white {
    left: 680px; top: 250px; width: 400px; height: 600px;
    background: linear-gradient(180deg, #fafafa, var(--paper) 60%, var(--paper-edge));
  }
  .cover--white .title-block { position: absolute; left: 0; top: 80px; width: 100%; text-align: center; color: var(--ink); }
  .cover--white .title-main { color: var(--royal); }
  .cover--white .chart-art {
    position: absolute; left: 70px; top: 250px; width: 290px; height: 240px;
    background: linear-gradient(135deg, rgba(227,35,28,.55), rgba(207,207,207,.7) 60%, rgba(228,228,228,.4));
  }
  .cover--white .grey-rule { position: absolute; left: 0; bottom: 88px; width: 100%; height: 8px; background: var(--rule-grey); }
  .cover--white .author-band {
    position: absolute; left: 0; bottom: 0; width: 100%; height: 88px;
    background: var(--royal-deep);
    display: flex; align-items: center; justify-content: center;
  }
  .cover--white .author { color: #fff; font-size: 22px; }

  .title-main { font-weight: 700; font-size: 40px; line-height: 1; letter-spacing: .5px; white-space: nowrap; }
  .title-sub { font-size: 25px; line-height: 1.25; margin-top: 12px; }
  .author { font-weight: 700; font-size: 26px; letter-spacing: 2px; }
</style>
</head>
<body>
<main class="canvas">

  <section class="cover cover--navy" aria-label="Navy and gold cover edition">
    <div class="pattern-field" role="img" aria-label="Faint geometric pattern across the top of the cover"></div>
    <div class="title-block">
      <h1 class="title-main">Creditor Remedies</h1>
      <p class="title-sub">Within Gulf<br>Trade Statutes</p>
    </div>
    <div class="chart-art" role="img" aria-label="Gold falling zigzag arrow cracking the ground"></div>
    <div class="band-rule"></div>
    <div class="author-band"><p class="author">YUSUF BIN TAREQ</p></div>
  </section>

  <section class="cover cover--white" aria-label="White and royal blue cover edition">
    <div class="title-block">
      <h2 class="title-main">Creditor Remedies</h2>
      <p class="title-sub">Within Gulf<br>Trade Statutes</p>
    </div>
    <div class="chart-art" role="img" aria-label="Red falling arrow over white bar chart, cracking the ground"></div>
    <div class="grey-rule"></div>
    <div class="author-band"><p class="author">YUSUF BIN TAREQ</p></div>
  </section>

</main>
</body>
</html>
```